Business Card Design for Occupational Medicine Start Up Company

We need to design a professional business card. We are a healthcare company providing occupational medicine services to blue collar industries. We are professional, efficient and high quality service providers.

Target Market(s)

Blue Collar Industry: Shipbuilding, Ports, Trucking Companies; The Executives and Safety Officers for these companies

Industry/Entity Type

Healthcare

Contact Information for Business Card

Logo, Name, Title, Email, Phone

Other font styles liked:
• Please match our Brand Guide

Requirements
Must have
• Our Company Colors and Logo

```html
<!DOCTYPE html>
<html lang="en">
<head>
<meta charset="utf-8">
<title>Crewline Clinics – Business Card</title>
<link href="https://fonts.googleapis.com/css2?family=Montserrat:wght@300;400;700;800&display=swap" rel="stylesheet">
<style>
  :root {
    --stage: #2b2b2d;
    --card: #2b3688;
    --card-tone: #3140a0;
    --ink: #ffffff;
  }
  * { margin: 0; padding: 0; box-sizing: border-box; }
  html, body { width: 1200px; height: 1015px; overflow: hidden; }
  body {
    background: var(--stage);
    font-family: "Montserrat", Arial, sans-serif;
    color: var(--ink);
    position: relative;
  }
  .card {
    position: absolute;
    left: 215px;
    width: 770px;
    height: 440px;
    background: var(--card);
    overflow: hidden;
    box-shadow: 0 14px 30px rgba(0,0,0,.55);
  }
  .card--front { top: 45px; }
  .card--back { top: 530px; }

  /* front */
  .wordmark {
    position: absolute;
    inset: 0;
    display: flex;
    flex-direction: column;
    align-items: center;
    justify-content: center;
    gap: 26px;
  }
  .wordmark__dot {
    width: 90px; height: 90px;
    border-radius: 50%;
    background: var(--ink);
  }
  .wordmark__name {
    font-weight: 700;
    font-size: 44px;
    letter-spacing: 2px;
    text-transform: uppercase;
    color: var(--ink);
    text-align: center;
    line-height: 1.1;
  }

  /* back */
  .brand-emboss {
    position: absolute;
    right: 70px; top: 60px;
    width: 320px; height: 320px;
    border-radius: 50%;
    background: var(--card-tone);
    box-shadow: inset 2px 2px 4px rgba(0,0,0,.25), inset -2px -2px 4px rgba(255,255,255,.06);
  }
  .holder {
    position: absolute;
    left: 70px; top: 170px;
  }
  .holder__name {
    font-size: 30px;
    text-transform: uppercase;
    letter-spacing: .5px;
    line-height: 1;
  }
  .holder__first { font-weight: 800; }
  .holder__last { font-weight: 300; }
  .holder__title {
    font-size: 15px;
    font-weight: 400;
    text-transform: uppercase;
    margin-top: 6px;
    letter-spacing: .4px;
  }
  .contact {
    list-style: none;
    margin-top: 46px;
    font-size: 17px;
    font-weight: 400;
    line-height: 1.55;
  }
  .contact li { display: flex; align-items: center; gap: 10px; }
  .contact svg { width: 17px; height: 17px; flex: none; }
</style>
</head>
<body>

<section class="card card--front" aria-label="Card front">
  <div class="wordmark">
    <div class="wordmark__dot"></div>
    <div class="wordmark__name">Crewline Clinics</div>
  </div>
</section>

<section class="card card--back" aria-label="Card back">
  <div class="brand-emboss" role="img" aria-label="Embossed brand symbol"></div>

  <div class="holder">
    <p class="holder__name"><span class="holder__first">Daniel</span> <span class="holder__last">Hayes</span></p>
    <p class="holder__title">Managing Director</p>

    <ul class="contact">
      <li>
        <svg viewBox="0 0 24 24" fill="none" stroke="#fff" stroke-width="2" stroke-linecap="round" stroke-linejoin="round" aria-hidden="true"><path d="M22 16.9v3a2 2 0 0 1-2.2 2 19.8 19.8 0 0 1-8.6-3.1 19.5 19.5 0 0 1-6-6A19.8 19.8 0 0 1 2.1 4.2 2 2 0 0 1 4.1 2h3a2 2 0 0 1 2 1.7c.1 1 .4 1.9.7 2.8a2 2 0 0 1-.5 2.1L8 9.9a16 16 0 0 0 6 6l1.3-1.3a2 2 0 0 1 2.1-.4c.9.3 1.8.6 2.8.7a2 2 0 0 1 1.7 2z"/></svg>
        044-987 654 321
      </li>
      <li>
        <svg viewBox="0 0 24 24" fill="none" stroke="#fff" stroke-width="2" stroke-linejoin="round" aria-hidden="true"><rect x="2" y="5" width="20" height="14" rx="1"/><path d="M2 6l10 7 10-7"/></svg>
        info@crewlineclinics.com
      </li>
      <li>
        <svg viewBox="0 0 24 24" fill="none" stroke="#fff" stroke-width="1.8" aria-hidden="true"><circle cx="12" cy="12" r="10"/><path d="M2 12h20M12 2c3 3 3 17 0 20M12 2c-3 3-3 17 0 20"/></svg>
        www.crewlineclinics.com
      </li>
    </ul>
  </div>
</section>

</body>
</html>
```